Electric mountain bike tours nz

We are an Electric Mountain bike tour company in New Zealand. We will be offering bike rental and guided tours around the Nelson region in New Zealand. I want our website to represent both Mountain biking and New Zealand with the colours layout and features. We want tabs for the following:
-1 about us
-2 what we offer
-3 bookings/contact
Under the about us tab will be who we are as a a company. I want the ability to add videos to each of these tabs as we move foward with videos of the tracks we will be riding. I want the website to be editable so I can add and remove videos/photos myself. Also "our bikes" will be under this tab.
Under the what we offer tab will be
-1 bike rental and pricing
-2 guided tours and pricing
-3 recommended package deals.
I want to able to put the tracks under the guided tours tab and select beginner/ intermediate/advanced and have the tracks in each of the following to match the rider level. Also to be able to have a small video of the track would be great in this section.
Bookings and contact tab
(Further information for this tab to be updated soon)
Coded - Design and coding required
1 page
- Silver ferns, kiwi, mountains

```html
<!DOCTYPE html>
<html lang="en">
<head>
<meta charset="utf-8">
<title>Ridgevolt – Electric Mountain Bike Tours in New Zealand</title>
<link href="https://fonts.googleapis.com/css2?family=Montserrat:wght@500;600;700;800&family=Open+Sans:wght@400;600;700&display=swap" rel="stylesheet">
<style>
:root{
  --blue:#1f7fe6;
  --blue-deep:#0f4fb8;
  --blue-light:#4fb0ff;
  --ink:#2a2a2a;
  --text:#5b5b5b;
  --white:#ffffff;
  --orange:#f47320;
  --orange-deep:#e05a10;
  --green:#2f9c3c;
  --green-deep:#21802d;
  --ult:#2d6fd0;
  --ult-deep:#1d56ad;
  --card:#2e2e2e;
  --card-line:#444;
  --forest:#1b2414;
  --paper:#f3f3f3;
}
*{margin:0;padding:0;box-sizing:border-box}
html,body{width:1200px;height:3184px;overflow:hidden;background:var(--white)}
body{font-family:"Open Sans",Arial,sans-serif;color:var(--text);position:relative}
a{text-decoration:none}
section,header,footer{position:absolute;left:0;width:1200px}
.photo{position:absolute}
.torn{position:absolute;left:0;width:1200px;display:block}
.btn{display:inline-block;background:linear-gradient(90deg,var(--blue-light),var(--blue));color:var(--white);font:600 17px "Open Sans",sans-serif;padding:0 34px;height:48px;line-height:48px;border-radius:24px}
.btn.outline{background:transparent;border:2px solid var(--white);line-height:36px}

/* header / hero */
.hero{top:0;height:760px;overflow:hidden}
.hero .photo{inset:0;background:linear-gradient(180deg,#6f9fd6 0%,#b8cde0 30%,#7a8f5a 58%,#5c6b32 80%,#3e4a22 100%)}
.brand{position:absolute;left:196px;top:8px;display:flex;align-items:center;gap:10px;z-index:2}
.brand .dot{width:22px;height:22px;border-radius:50%;background:var(--white)}
.brand span{font:800 26px "Montserrat",sans-serif;color:var(--white);letter-spacing:1px}
.nav{position:absolute;right:200px;top:48px;display:flex;gap:30px;list-style:none;z-index:2}
.nav a{font:700 14px "Montserrat",sans-serif;color:var(--ink)}
.nav .active a{color:var(--white)}
.hero h1{position:absolute;left:0;width:1200px;top:300px;text-align:center;color:var(--white);font:700 42px/52px "Montserrat",sans-serif;letter-spacing:1px}
.hero .btn{position:absolute;left:544px;top:408px;height:40px;line-height:40px;font-size:15px}
.slider-dots{position:absolute;left:1068px;top:336px;display:flex;flex-direction:column;gap:10px;list-style:none}
.slider-dots li{width:12px;height:12px;border-radius:50%;background:rgba(255,255,255,.6)}
.slider-dots li:first-child{background:var(--white)}

/* section titles */
.title{font:600 30px "Montserrat",sans-serif;color:var(--ink);text-align:center;letter-spacing:1px}
.peak{display:block;margin:0 auto 4px}

/* about */
.about{top:740px;height:420px}
.about .fern{position:absolute;left:60px;top:90px;width:300px;height:300px;border-radius:50%;background:radial-gradient(circle,#e9ecef 0%,rgba(233,236,239,0) 70%)}
.about .title{position:absolute;top:20px;left:0;width:1200px}
.about .copy{position:absolute;left:345px;top:86px;width:480px;text-align:center;font-size:14px;line-height:22px}
.about .copy p+p{margin-top:10px}
.about .btn{position:absolute;left:520px;top:258px}
.about .bike{left:850px;top:60px;width:340px;height:220px;background:linear-gradient(135deg,#e8e8e8,#9a9a9a 60%,#d4d4d4);border-radius:6px}

/* video */
.video{top:1160px;height:470px;background:linear-gradient(180deg,var(--blue) 0%,#2f90ee 45%,var(--blue-deep) 100%)}
.video .peaks-bg{left:0;top:60px;width:1200px;height:360px;background:linear-gradient(180deg,rgba(255,255,255,0) 0%,rgba(190,220,255,.25) 50%,rgba(10,50,140,.2) 100%)}
.video h2{position:absolute;left:208px;top:150px;color:var(--white);font:600 26px "Montserrat",sans-serif}
.video .peak{position:absolute;left:208px;top:118px}
.video p{position:absolute;left:208px;top:196px;width:300px;color:#e6f1ff;font-size:13px;line-height:20px}
.video .btn{position:absolute;left:208px;top:358px;height:40px;font-size:15px}
.video .frame{position:absolute;left:568px;top:112px;width:346px;height:290px;border:3px solid rgba(255,255,255,.75)}
.video .thumb{left:8px;top:8px;width:324px;height:268px;background:linear-gradient(160deg,#f0c070 0%,#c07840 35%,#4a3a2a 75%,#2a2218 100%)}
.video .play{position:absolute;left:134px;top:100px}

/* packages */
.packages{top:1630px;height:860px;background:linear-gradient(180deg,#ffffff 0%,#ffffff 45%,#dfe6ee 70%,#b9c4cf 100%)}
.packages .mountains{left:0;top:420px;width:1200px;height:440px;background:linear-gradient(180deg,rgba(255,255,255,0),rgba(140,155,170,.55) 60%,rgba(90,100,110,.6))}
.packages .title{position:absolute;top:100px;left:0;width:1200px}
.kiwi-a{left:258px;top:98px;width:56px;height:60px;border-radius:50% 50% 40% 40%;background:linear-gradient(#8a6a40,#5a4326)}
.tabs{position:absolute;top:186px;left:0;width:1200px;display:flex;justify-content:center;gap:6px;list-style:none}
.tabs li{font:700 10px "Montserrat",sans-serif;color:var(--ink);padding:6px 12px;border:1px solid #ccc}
.tabs li.on{background:var(--ink);color:var(--white);border-color:var(--ink)}
.plan{position:absolute;width:280px;background:var(--card);color:#ddd;text-align:center}
.plan .head{height:160px;position:relative;color:var(--white)}
.plan .name{height:36px;line-height:36px;font:700 18px "Montserrat",sans-serif}
.plan .price{position:absolute;left:50%;top:58px;transform:translateX(-50%);width:92px;height:92px;border-radius:50%;display:flex;align-items:center;justify-content:center;font:600 44px "Montserrat",sans-serif}
.plan .price sup{font-size:18px;margin-top:-14px}
.plan .price small{font:400 9px "Open Sans",sans-serif;align-self:flex-end;margin-bottom:28px;margin-left:2px}
.plan h3{font:600 13px "Montserrat",sans-serif;color:var(--white);padding:22px 0 12px}
.plan ul{list-style:none;margin:0 24px}
.plan li{font-size:11px;line-height:30px;border-top:1px solid var(--card-line)}
.plan .book{display:inline-block;margin:16px 0 24px;background:var(--green);color:var(--white);font:700 11px "Montserrat",sans-serif;padding:8px 16px;border-radius:14px}
.plan.starter{left:176px;top:270px}
.plan.starter .head{background:var(--orange)} .plan.starter .name{background:var(--orange-deep)} .plan.starter .price{background:var(--orange-deep)}
.plan.standard{left:458px;top:240px;width:290px;box-shadow:0 6px 20px rgba(0,0,0,.35);z-index:2}
.plan.standard .head{background:var(--green);height:190px} .plan.standard .name{background:var(--green-deep)} .plan.standard .price{background:var(--green-deep);top:70px}
.plan.ultimate{left:748px;top:270px;width:264px}
.plan.ultimate .head{background:var(--ult)} .plan.ultimate .name{background:var(--ult-deep)} .plan.ultimate .price{background:var(--ult-deep)}
.kiwi-b{left:1030px;top:760px;width:120px;height:170px;z-index:3;border-radius:50% 50% 40% 40%;background:linear-gradient(#8a6a40,#4e3a22)}

/* booking */
.booking{top:2470px;height:540px;background:var(--forest)}
.booking .forest{inset:0;background:linear-gradient(90deg,#0f140c 0%,#1f2b16 40%,#3c5626 70%,#2a3a1c 100%)}
.booking .bike{left:560px;top:180px;width:520px;height:300px;background:linear-gradient(150deg,#4f7a2e,#c27a2a 55%,#3a2e1e);opacity:.75;border-radius:6px}
.booking h2{position:absolute;left:214px;top:130px;color:var(--white);font:600 30px "Montserrat",sans-serif;letter-spacing:1px}
.booking p{position:absolute;left:214px;top:186px;width:300px;color:#d7dccf;font-size:13px;line-height:20px}
.booking .btn{position:absolute;left:214px;top:410px}

/* footer */
.footer{top:2980px;height:204px;background:var(--paper)}
.footer .brand{left:196px;top:40px}
.footer .brand .dot{background:var(--ink)}
.footer .brand span{color:var(--ink);font-size:20px}
.footer .nav{right:auto;left:380px;top:46px;gap:24px}
.footer .nav a{font-size:13px}
.social{position:absolute;left:902px;top:40px;display:flex;gap:8px;list-style:none}
.social li{width:28px;height:28px;border-radius:50%;background:var(--ink)}
.copyright{position:absolute;left:380px;top:84px;font-size:11px;color:#777}
</style>
</head>
<body>

<header class="hero">
  <div class="photo" role="img" aria-label="Electric mountain bike parked by a trail sign on a hilltop above a lake and mountains"></div>
  <a class="brand" href="#"><i class="dot"></i><span>RIDGEVOLT</span></a>
  <ul class="nav">
    <li class="active"><a href="#">HOME</a></li>
    <li><a href="#">ABOUT US</a></li>
    <li><a href="#">WHAT WE OFFER</a></li>
    <li><a href="#">BOOKINGS</a></li>
    <li><a href="#">CONTACT US</a></li>
  </ul>
  <h1>ELECTRIC MOUNTAIN<br>BIKE TOURS IN NEW ZEALAND</h1>
  <a class="btn" href="#">Click here</a>
  <ul class="slider-dots"><li></li><li></li><li></li><li></li></ul>
  <svg class="torn" style="top:700px" width="1200" height="60" viewBox="0 0 1200 60" preserveAspectRatio="none"><path fill="#fff" d="M0 30 L40 22 L80 34 L120 18 L170 30 L220 20 L260 36 L310 24 L360 32 L410 14 L460 30 L510 22 L560 36 L610 20 L660 30 L710 16 L760 32 L810 22 L860 34 L910 18 L960 30 L1010 22 L1060 36 L1110 20 L1160 30 L1200 24 L1200 60 L0 60 Z"/></svg>
</header>

<section class="about">
  <div class="fern" role="img" aria-label="Faint silver fern decoration"></div>
  <div class="title">
    <svg class="peak" width="40" height="20" viewBox="0 0 40 20"><path d="M0 20 L14 4 L20 10 L27 2 L40 20 Z" fill="none" stroke="#1f7fe6" stroke-width="2.5"/></svg>
    ABOUT US
  </div>
  <div class="copy">
    <p>We are a small team of riders guiding electric mountain bike tours through the hills, forests and coastal tracks of the Nelson region, sharing trails we love.</p>
    <p>Hire one of our bikes for the day or join a guided ride matched to your level, from gentle valley loops to steep alpine descents with views across the bay.</p>
  </div>
  <a class="btn" href="#">Read More</a>
  <div class="photo bike" role="img" aria-label="Grey and orange electric mountain bike"></div>
</section>

<section class="video">
  <svg class="torn" style="top:-10px" width="1200" height="40" viewBox="0 0 1200 40" preserveAspectRatio="none"><path fill="#fff" d="M0 0 H1200 V20 L1150 28 L1100 16 L1050 30 L990 18 L930 26 L870 14 L810 30 L750 20 L690 28 L630 16 L570 30 L510 18 L450 26 L390 14 L330 30 L270 20 L210 28 L150 16 L90 30 L40 18 L0 26 Z"/></svg>
  <div class="photo peaks-bg" role="img" aria-label="Blue tinted mountain range"></div>
  <svg class="peak" width="40" height="20" viewBox="0 0 40 20"><path d="M0 20 L14 4 L20 10 L27 2 L40 20 Z" fill="none" stroke="#fff" stroke-width="2.5"/></svg>
  <h2>WATCH OUR VIDEO</h2>
  <p>Take a look at the tracks we ride. Short clips of each trail help you pick the tour that suits your pace and experience before you book.</p>
  <a class="btn outline" href="#">Click here</a>
  <div class="frame">
    <div class="photo thumb" role="img" aria-label="Rider on a mountain trail at sunset"></div>
    <svg class="play" width="60" height="60" viewBox="0 0 60 60"><circle cx="30" cy="30" r="28" fill="rgba(255,255,255,.9)"/><path d="M24 18 L42 30 L24 42 Z" fill="#333"/></svg>
  </div>
  <svg class="torn" style="top:440px" width="1200" height="40" viewBox="0 0 1200 40" preserveAspectRatio="none"><path fill="#fff" d="M0 20 L50 12 L100 24 L160 10 L220 22 L280 14 L340 26 L400 12 L460 22 L520 10 L580 24 L640 14 L700 26 L760 12 L820 22 L880 10 L940 24 L1000 14 L1060 26 L1120 12 L1200 20 V40 H0 Z"/></svg>
</section>

<section class="packages">
  <div class="photo mountains" role="img" aria-label="Snow covered mountain range"></div>
  <div class="photo kiwi-a" role="img" aria-label="Kiwi bird"></div>
  <div class="title">
    <svg class="peak" width="40" height="20" viewBox="0 0 40 20"><path d="M0 20 L14 4 L20 10 L27 2 L40 20 Z" fill="none" stroke="#1f7fe6" stroke-width="2.5"/></svg>
    OUR PACKAGE
  </div>
  <ul class="tabs"><li>BIKE RENTAL</li><li>GUIDED TOURS</li><li class="on">ALL PACKAGES</li></ul>

  <article class="plan starter">
    <div class="head"><div class="name">STARTER</div><div class="price"><sup>$</sup>19<small>/month</small></div></div>
    <h3>SINGLE PLACE TRAVEL</h3>
    <ul><li>Electric bike hire</li><li>Helmet and gloves</li><li>Local trail map</li><li>Trail snacks</li><li>Photos of your ride</li><li>Bike wash station</li></ul>
    <span class="book">BOOK NOW</span>
  </article>
  <article class="plan standard">
    <div class="head"><div class="name">STANDARD</div><div class="price"><sup>$</sup>39<small>/month</small></div></div>
    <h3>THREE PLACE TRAVEL</h3>
    <ul><li>Electric bike hire</li><li>Local trail guide</li><li>Helmet and gloves</li><li>Lunch on the trail</li><li>Photos of your ride</li><li>Return transfer</li></ul>
    <span class="book">BOOK NOW</span>
  </article>
  <article class="plan ultimate">
    <div class="head"><div class="name">ULTIMATE</div><div class="price"><sup>$</sup>59<small>/month</small></div></div>
    <h3>FIVE PLACE TRAVEL</h3>
    <ul><li>Premium bike hire</li><li>Private trail guide</li><li>Full riding kit</li><li>Lunch on the trail</li><li>Video of your ride</li><li>Return transfer</li></ul>
    <span class="book">BOOK NOW</span>
  </article>
  <div class="photo kiwi-b" role="img" aria-label="Kiwi bird standing at the edge of the section"></div>
</section>

<section class="booking">
  <svg class="torn" style="top:-12px" width="1200" height="40" viewBox="0 0 1200 40" preserveAspectRatio="none"><path fill="#b9c4cf" d="M0 0 H1200 V22 L1140 30 L1080 16 L1020 28 L960 14 L900 30 L840 18 L780 26 L720 12 L660 28 L600 18 L540 30 L480 14 L420 26 L360 16 L300 30 L240 18 L180 28 L120 14 L60 26 L0 18 Z"/></svg>
  <div class="photo forest" role="img" aria-label="Dark native forest with tall tree trunks"></div>
  <div class="photo bike" role="img" aria-label="Orange electric mountain bike by a trail sign in the bush"></div>
  <h2>OUR BOOKING</h2>
  <p>Bookings open for the coming season. Choose a date, pick your track and we will have bikes charged and ready when you arrive in Nelson.</p>
  <a class="btn" href="#">Read More</a>
</section>

<footer class="footer">
  <svg class="torn" style="top:-22px" width="1200" height="40" viewBox="0 0 1200 40" preserveAspectRatio="none"><path fill="#f3f3f3" d="M0 22 L60 12 L120 26 L180 14 L240 24 L300 10 L360 26 L420 16 L480 28 L540 12 L600 24 L660 14 L720 28 L780 12 L840 22 L900 10 L960 26 L1020 16 L1080 28 L1140 14 L1200 22 V40 H0 Z"/></svg>
  <a class="brand" href="#"><i class="dot"></i><span>RIDGEVOLT</span></a>
  <ul class="nav">
    <li><a href="#">HOME</a></li><li><a href="#">ABOUT US</a></li><li><a href="#">WHAT WE OFFER</a></li><li><a href="#">BOOKINGS</a></li><li><a href="#">CONTACT US</a></li>
  </ul>
  <ul class="social"><li></li><li></li><li></li><li></li></ul>
  <p class="copyright">© 2018 Ridgevolt Tours. All rights reserved.</p>
</footer>

</body>
</html>
```